Business card design needed

am looking for a fun and funky design to match our moto, seriously fun swimwear and fashion for girls.

We manufacture and retail girls swimwear and fashion in Australia. Our designs are fun loving and funky. I would like to use bright fuschia to match our website www.breezlumina.com.au. We target a higher end market so need it to reflect this.

Industry/Entity Type

Fashion

Contact Information for Business Card

Breez Lumina logo,
Delia Morwen
(07) 32451790
admin@breezlumina.com.au
www.breezlumina.com.au

Logo Text

Breez Lumina

```html
<!DOCTYPE html>
<html lang="en">
<head>
<meta charset="utf-8">
<title>Breez Lumina — Business Card</title>
<link rel="stylesheet" href="https://fonts.googleapis.com/css2?family=Open+Sans:wght@400;600;700&display=swap">
<style>
  :root {
    --backdrop: #2b2b2d;
    --fuchsia: #d63a8a;
    --fuchsia-light: #ea5aa3;
    --fuchsia-deep: #c12c79;
    --blush: #f6cadc;
    --plum: #b0246b;
    --white: #ffffff;
  }
  * { box-sizing: border-box; margin: 0; padding: 0; }
  html, body {
    width: 1200px; height: 900px; overflow: hidden;
    background: var(--backdrop);
    font-family: "Open Sans", Arial, sans-serif;
  }
  .stage {
    position: relative; width: 1200px; height: 900px;
    display: flex; align-items: center; justify-content: center; gap: 50px;
  }
  .card {
    position: relative; width: 540px; height: 310px; overflow: hidden;
    box-shadow: 0 10px 30px rgba(0,0,0,.45);
  }
  .card-front {
    background: radial-gradient(ellipse at 62% 40%, var(--fuchsia-light) 0%, var(--fuchsia) 55%, var(--fuchsia-deep) 100%);
    display: flex; align-items: center; justify-content: center;
  }
  .front-brand {
    color: var(--white); font-size: 52px; font-weight: 400; letter-spacing: 1px;
  }
  .card-back {
    background: radial-gradient(ellipse at 55% 60%, var(--fuchsia-light) 0%, var(--fuchsia) 60%, var(--fuchsia-deep) 100%);
  }
  .brand-band {
    position: absolute; top: 0; left: 0; right: 0; height: 118px;
    background: var(--blush);
    display: flex; align-items: center; padding-left: 80px; gap: 14px;
    box-shadow: 0 3px 8px rgba(0,0,0,.18);
  }
  .brand-dot {
    width: 34px; height: 34px; border-radius: 50%; background: var(--fuchsia);
  }
  .brand-name {
    color: var(--plum); font-size: 40px; font-weight: 400;
  }
  .holder-name {
    position: absolute; top: 150px; left: 0; right: 0; text-align: center;
    color: var(--white); font-size: 32px; font-weight: 700;
  }
  .contact-row {
    position: absolute; bottom: 34px; left: 0; right: 0;
    display: flex; justify-content: center; align-items: center;
    color: var(--white); font-size: 13px;
  }
  .contact-row .divider {
    width: 1px; height: 18px; background: rgba(255,255,255,.8); margin: 0 14px;
  }
</style>
</head>
<body>
  <main class="stage">
    <section class="card card-front" aria-label="Card front">
      <p class="front-brand">Breez Lumina</p>
    </section>
    <section class="card card-back" aria-label="Card back">
      <header class="brand-band">
        <span class="brand-dot"></span>
        <span class="brand-name">Breez Lumina</span>
      </header>
      <h1 class="holder-name">Delia Morwen</h1>
      <p class="contact-row">
        <span class="phone">(07) 32451790</span>
        <span class="divider"></span>
        <span class="email">admin@breezlumina.com.au</span>
        <span class="divider"></span>
        <span class="web">breezlumina.com.au</span>
      </p>
    </section>
  </main>
</body>
</html>
```